Professional & attention grabbing.

A business card design, front and back. I already have a logo I will attach, but I am open to something new as well.
Things to include:
Name:
Title:
Phone:
Email:
Wanting something that is professional but attention grabbing.
Also we do a lot of work using drones on natural gas pipelines (leading the future)if you want to include any of that. I'm open to ideas.
Target Market(s)
Natural gas transmission industry / greenhouse gas mitigation industry
Industry/Entity Type
Business
Colors
Designer to choose colors to be used in the design.
Look and feel
Each slider illustrates characteristics of the customer's brand and the style your logo design should communicate.

```html
<!DOCTYPE html>
<html lang="en">
<head>
<meta charset="utf-8">
<title>Meridian Inspections – Business Card</title>
<link rel="stylesheet" href="https://fonts.googleapis.com/css2?family=Arimo:wght@400;700&display=swap">
<style>
  :root {
    --red: #c8202a;
    --white: #ffffff;
    --ink: #2a2a2a;
    --line: #e49aa0;
    --stage: #e6e7e9;
    --pipe-blue: #bfe0f0;
    --pipe-pink: #f4b6d2;
    --pipe-yellow: #f7e7a6;
    --pipe-teal: #a9dccb;
  }
  * { box-sizing: border-box; margin: 0; padding: 0; }
  html, body { width: 1200px; height: 900px; overflow: hidden; }
  body {
    background: var(--stage);
    font-family: "Arimo", Arial, sans-serif;
    position: relative;
  }
  .card {
    position: absolute;
    left: 250px;
    width: 700px;
    height: 400px;
    background: var(--white);
    border-radius: 22px;
    overflow: hidden;
    box-shadow: 0 6px 18px rgba(0,0,0,.15);
  }
  .card--back { top: 35px; }
  .card--front { top: 465px; }

  .pipe-pattern {
    position: absolute;
    background: linear-gradient(120deg, var(--pipe-blue) 0%, var(--pipe-pink) 30%, var(--pipe-yellow) 60%, var(--pipe-teal) 100%);
    opacity: .55;
  }

  /* back */
  .card--back .pipe-pattern { inset: 0; }
  .back-corner-top {
    position: absolute; right: 0; top: 0; width: 70px; height: 210px;
    background: var(--red); border-bottom-left-radius: 26px;
  }
  .back-corner-left {
    position: absolute; left: 0; bottom: 0; width: 90px; height: 150px;
    background: var(--red); border-top-right-radius: 26px;
  }
  .back-band {
    position: absolute; left: 0; right: 0; bottom: 0; height: 82px;
    background: var(--red);
    display: flex; align-items: center; justify-content: flex-end;
    padding-right: 48px;
    color: var(--white); font-size: 26px; letter-spacing: .5px; text-transform: uppercase;
  }
  .back-logo {
    position: absolute; left: 250px; top: 80px; width: 200px; height: 200px;
    background: var(--white); border-radius: 30px;
    box-shadow: 0 4px 14px rgba(0,0,0,.18);
    display: flex; align-items: center; justify-content: center;
  }
  .brand-name {
    color: var(--ink); font-weight: 700; font-size: 34px;
    display: flex; align-items: center; gap: 10px;
  }
  .brand-mark { width: 16px; height: 16px; background: var(--red); }

  /* front */
  .front-pill {
    position: absolute; left: 0; top: 52px; width: 300px; height: 50px;
    background: var(--red); border-radius: 0 16px 16px 0;
    color: var(--white); font-size: 20px; text-transform: uppercase;
    display: flex; align-items: center; padding-left: 26px; letter-spacing: .4px;
  }
  .front-rule { position: absolute; left: 0; right: 0; height: 2px; background: var(--line); }
  .front-rule--top { top: 104px; }
  .front-rule--bottom { top: 296px; }
  .front-tagline {
    position: absolute; left: 360px; top: 16px;
    color: var(--red); font-size: 19px; line-height: 22px;
  }
  .card--front .pipe-pattern { left: 0; right: 0; top: 112px; height: 176px; }
  .front-logo {
    position: absolute; left: 400px; top: 112px; width: 210px; height: 150px;
    background: var(--white); border-radius: 26px;
    box-shadow: 0 4px 14px rgba(0,0,0,.18);
    display: flex; align-items: center; justify-content: center;
  }
  .front-logo .brand-name { font-size: 30px; }
  .contact {
    position: absolute; display: flex; align-items: center; gap: 10px;
    color: var(--red); font-size: 16px; white-space: nowrap;
  }
  .contact--phone { left: 270px; top: 330px; }
  .contact--email { left: 420px; top: 312px; text-transform: uppercase; font-size: 15px; }
  .contact svg { width: 26px; height: 26px; flex: none; }
  .person { position: absolute; left: 36px; top: 322px; color: var(--red); }
  .person-name { font-size: 34px; font-weight: 700; line-height: 36px; }
  .person-title { font-size: 20px; font-weight: 700; margin-left: 70px; }
</style>
</head>
<body>

<section class="card card--back">
  <div class="pipe-pattern" role="img" aria-label="Pastel pipeline network pattern"></div>
  <div class="back-corner-top"></div>
  <div class="back-corner-left"></div>
  <div class="back-band">Meridian Inspections</div>
  <div class="back-logo">
    <span class="brand-name"><span class="brand-mark"></span>Meridian</span>
  </div>
</section>

<section class="card card--front">
  <div class="front-tagline">Natural gas<br>Transmission industry</div>
  <div class="front-pill">Meridian Inspections</div>
  <div class="front-rule front-rule--top"></div>
  <div class="pipe-pattern" role="img" aria-label="Pastel pipeline network pattern"></div>
  <div class="front-logo">
    <span class="brand-name"><span class="brand-mark"></span>Meridian</span>
  </div>
  <div class="front-rule front-rule--bottom"></div>

  <div class="contact contact--email">
    <svg viewBox="0 0 26 26" aria-hidden="true"><circle cx="13" cy="13" r="13" fill="#c8202a"/><rect x="6.5" y="8.5" width="13" height="9" fill="none" stroke="#fff" stroke-width="1.6"/><path d="M6.5 8.5 13 14l6.5-5.5" fill="none" stroke="#fff" stroke-width="1.6"/></svg>
    <span>info@meridianinsp.com</span>
  </div>
  <div class="contact contact--phone">
    <svg viewBox="0 0 26 26" aria-hidden="true"><circle cx="13" cy="13" r="13" fill="#c8202a"/><path d="M9 7.5c-1 .6-1.6 1.6-1.2 3 1 3.6 3.9 6.6 7.6 7.6 1.4.4 2.4-.2 3-1.2l-2.3-2-1.5 1c-1.6-.8-2.8-2-3.6-3.6l1-1.5z" fill="#fff"/></svg>
    <span>55501 24680</span>
  </div>

  <div class="person">
    <div class="person-name">Alan Porter</div>
    <div class="person-title">Director</div>
  </div>
</section>

</body>
</html>
```